Landing page design for my current website

I need a landing page designed for my Wordpress website. My website is Velmorquay.com, and I need a page that will serve as a landing page for online ads I run. Please follow the color scheme of the current website

This web page will be targeted towards real estate owners who are looking for a property manager. Above the fold needs to have a CTA form headlined with "As a Rental Property Owner, I Want More Protection, Less Stress, and Drama-Free Living"

A few highlights that can be listed beyond the CTA and fold

- Comprehensive Property Management
Full-service management covering tenant placement, leasing, maintenance, and inspections.

Maximized Rental Income
Proven strategies to optimize rental rates and minimize vacancies, ensuring higher ROI.

Stress-Free Management
We handle all tenant interactions, maintenance requests, and property issues, so you don't have to.

Experienced Team
Over a decade of experience in managing single-family homes, small multifamily units, and apartment complexes.

Advanced Technology
Utilize cutting-edge property management software for efficient communication, rent collection, and maintenance tracking.

Tenant Screening and Placement
Thorough background checks and tenant screening processes to ensure reliable and responsible tenants.

Regular Property Inspections
Routine inspections to maintain property condition and address issues before they become costly problems.

Legal Compliance
Expertise in local and federal rental laws to keep your properties compliant and avoid legal hassles.

Transparent Reporting
Detailed monthly reports and financial statements to keep you informed about your property's performance.

Personalized Service
Tailored management plans to meet the unique needs of your properties and investment goals.
Effective Tenant Conflict Resolution
Skilled in handling challenging tenant situations, ensuring conflicts are resolved quickly and professionally to maintain a peaceful living environment and protect your investment.

```html
<!DOCTYPE html>
<html lang="en">
<head>
<meta charset="utf-8">
<title>Velmorquay Realty – Property Management</title>
<link href="https://fonts.googleapis.com/css2?family=Montserrat:wght@400;500;600;700&display=swap" rel="stylesheet">
<style>
:root{
  --navy:#12447c;
  --navy-dark:#0d3460;
  --ink:#111111;
  --page:#f3f3f3;
  --white:#ffffff;
  --grey:#8a8a8a;
  --text:#222222;
}
*{box-sizing:border-box;margin:0;padding:0}
html,body{width:1200px;height:2236px;overflow:hidden}
body{position:relative;background:var(--page);font-family:'Montserrat',sans-serif;color:var(--text)}
.abs{position:absolute}
.hero{left:0;top:0;width:1200px;height:608px;border-bottom-left-radius:90px;border-bottom:7px solid var(--navy);overflow:hidden}
.hero-photo{position:absolute;inset:0;background:linear-gradient(100deg,#07090d 0%,#15202c 30%,#5b5f66 55%,#8b7a68 70%,#8fb0d4 85%,#c9d8e6 100%)}
.hero-shade{position:absolute;inset:0;background:linear-gradient(90deg,rgba(0,0,0,.75) 0%,rgba(0,0,0,.35) 45%,rgba(0,0,0,0) 70%)}
.callbar{right:0;top:0;width:427px;height:48px;background:var(--navy);clip-path:polygon(0 0,100% 0,100% 100%,28px 100%);color:var(--white);font-size:13px;font-weight:500;display:flex;align-items:center;padding-left:104px;gap:18px}
.brand{left:90px;top:66px;display:flex;align-items:center;gap:12px;color:var(--white);font-weight:700;font-size:27px;letter-spacing:.5px}
.brand-dot{width:46px;height:46px;border:3px solid var(--white);border-radius:50%}
.nav{left:618px;top:80px;display:flex;gap:6px;font-size:13px;font-weight:500;color:var(--white)}
.nav a{color:inherit;text-decoration:none;padding:5px 8px 5px 8px;margin-right:14px}
.nav a.active{background:var(--navy);margin-right:8px}
.hero-title{left:87px;top:203px;color:var(--white);font-weight:500;font-size:26px;letter-spacing:.3px}
.hero-title strong{font-size:32px;font-weight:500}
.hero-copy{left:88px;top:266px;width:560px;color:var(--white);font-size:15.5px;line-height:39px;font-weight:500}
.btn{background:var(--navy);color:var(--white);font-weight:600;border-radius:40px;display:flex;align-items:center;justify-content:center;text-transform:uppercase}
.hero-btn{left:88px;top:413px;width:292px;height:62px;font-size:18px}
.form-card{left:675px;top:166px;width:437px;height:523px;background:var(--white);border-top-right-radius:60px;border-bottom-left-radius:85px;box-shadow:0 6px 18px rgba(0,0,0,.12)}
.form-head{position:absolute;left:0;top:36px;width:437px;text-align:center;font-size:18px;font-weight:600;line-height:40px;color:var(--ink)}
.form-head .blue{color:var(--navy)}
.field{position:absolute;left:34px;width:369px;border-bottom:1.5px solid #333;font-size:16px;font-weight:500;color:var(--ink);padding-bottom:6px}
.send{position:absolute;left:127px;top:429px;width:184px;height:52px;font-size:16px}
.sec-title{left:0;top:702px;width:1200px;text-align:center;font-size:34px;color:var(--navy);font-weight:400;letter-spacing:.5px}
.sec-title strong{font-weight:700}
.highlight{left:449px;top:792px;width:302px;height:345px;background:var(--navy);border-top-right-radius:50px;border-bottom-left-radius:50px}
.svc{width:300px;text-align:center}
.svc-icon{width:117px;height:117px;border-radius:50%;background:var(--navy);margin:0 auto;box-shadow:0 4px 0 var(--grey),inset 0 0 0 1px #2a5a91}
.svc-title{margin-top:27px;font-size:16.5px;font-weight:500;color:var(--navy);line-height:29px;text-transform:uppercase}
.svc-text{margin-top:5px;font-size:11.5px;line-height:29px;color:var(--ink);font-weight:500}
.svc.on .svc-icon{background:var(--white);box-shadow:0 4px 0 var(--grey)}
.svc.on .svc-title,.svc.on .svc-text{color:var(--white)}
.pager{left:0;top:1828px;width:1200px;display:flex;justify-content:center;align-items:center;gap:14px;font-size:15px;font-weight:500;color:#444}
.pager .num{width:38px;height:38px;border:1px solid #444;border-radius:50%;display:flex;align-items:center;justify-content:center}
.pager .num.cur{background:var(--navy);border-color:var(--navy);color:var(--white)}
.pager .word{margin:0 22px}
.footer{left:0;top:1936px;width:1200px;height:300px;background:#000;border-top:6px solid var(--navy);border-top-right-radius:130px}
.footer-inner{position:absolute;inset:0;border-top-right-radius:130px;border-right:5px solid var(--navy)}
.foot-brand{left:0;top:70px;width:1200px;display:flex;justify-content:center;align-items:center;gap:12px;color:var(--white);font-weight:700;font-size:27px}
.foot-links{left:0;top:168px;width:1200px;text-align:center;color:var(--white);font-size:15.5px;font-weight:500;word-spacing:2px}
.foot-links span{margin:0 22px}
.copy{left:0;top:231px;width:1200px;text-align:center;color:var(--white);font-size:12.5px;font-weight:500}
.copy span{margin:0 18px}
</style>
</head>
<body>

<section class="abs hero">
  <div class="hero-photo" role="img" aria-label="Modern multi-storey apartment building with balconies against an evening sky"></div>
  <div class="hero-shade"></div>
</section>

<div class="abs callbar">
  <svg width="14" height="14" viewBox="0 0 24 24" aria-hidden="true"><path fill="#fff" d="M6.6 10.8a15 15 0 0 0 6.6 6.6l2.2-2.2a1 1 0 0 1 1-.25 11.4 11.4 0 0 0 3.6.57 1 1 0 0 1 1 1V20a1 1 0 0 1-1 1A17 17 0 0 1 3 4a1 1 0 0 1 1-1h3.5a1 1 0 0 1 1 1c0 1.25.2 2.45.57 3.57a1 1 0 0 1-.25 1z"/></svg>
  <span>CALL OR TEXT 555.014.2286</span>
</div>

<div class="abs brand"><span class="brand-dot"></span>VELMORQUAY REALTY</div>

<nav class="abs nav">
  <a class="active">HOME</a><a>RESIDENTS</a><a>INVESTORS</a><a>COMMUNITIES</a><a>CONTACT US</a>
</nav>

<h1 class="abs hero-title">HOMES &amp; APARTMENTS <strong>FOR RENT</strong></h1>
<p class="abs hero-copy">Velmorquay, Inc. offers affordable, safe, up-to-date housing options in the Bloomsburg, Danville, and Berwick Pennsylvania markets. Contact us today if you’re looking for your next rental.</p>
<div class="abs btn hero-btn">View Available Rentals</div>

<form class="abs form-card">
  <h2 class="form-head"><span class="blue">AS A RENTAL PROPERTY OWNER, I WANT<br>MORE PROTECTION, LESS STRESS,</span> AND<br>DRAMA-FREE LIVING</h2>
  <div class="field" style="top:190px">FULL NAME*</div>
  <div class="field" style="top:259px">EMAIL ADDRESS*</div>
  <div class="field" style="top:328px;height:47px">MESSAGE*</div>
  <div class="btn send">Send Message</div>
</form>

<h2 class="abs sec-title">OUR <strong>SERVICES</strong></h2>

<div class="abs highlight"></div>

<div class="abs svc" style="left:115px;top:821px">
  <div class="svc-icon" role="img" aria-label="Property management icon"></div>
  <h3 class="svc-title">Comprehensive Property<br>Management</h3>
  <p class="svc-text">Full-service management covering<br>tenant placement, leasing,<br>maintenance, and inspections.</p>
</div>
<div class="abs svc on" style="left:450px;top:830px">
  <div class="svc-icon" role="img" aria-label="Rental income icon"></div>
  <h3 class="svc-title" style="margin-top:29px">Maximized Rental Income</h3>
  <p class="svc-text">Proven strategies to optimize rental<br>rates and minimize vacancies,<br>ensuring higher ROI.</p>
</div>
<div class="abs svc" style="left:785px;top:821px">
  <div class="svc-icon" role="img" aria-label="Stress-free icon"></div>
  <h3 class="svc-title">Stress-Free Management</h3>
  <p class="svc-text">We handle all tenant interactions,<br>maintenance requests, and property<br>issues, so you don't have to.</p>
</div>

<div class="abs svc" style="left:115px;top:1183px">
  <div class="svc-icon" role="img" aria-label="Team icon"></div>
  <h3 class="svc-title">Experienced Team</h3>
  <p class="svc-text">Over a decade of experience in<br>managing single-family homes,<br>small multifamily units, and<br>apartment complexes.</p>
</div>
<div class="abs svc" style="left:450px;top:1183px">
  <div class="svc-icon" role="img" aria-label="Technology icon"></div>
  <h3 class="svc-title">Advanced Technology</h3>
  <p class="svc-text">Utilize cutting-edge property<br>management software for efficient<br>communication, rent collection, and<br>maintenance tracking.</p>
</div>
<div class="abs svc" style="left:785px;top:1183px">
  <div class="svc-icon" role="img" aria-label="Key and handshake icon"></div>
  <h3 class="svc-title">Tenant Screening &amp; Placement</h3>
  <p class="svc-text">Thorough background checks and<br>tenant screening processes to<br>ensure reliable and responsible<br>tenants.</p>
</div>

<div class="abs svc" style="left:115px;top:1507px">
  <div class="svc-icon" role="img" aria-label="Building inspection icon"></div>
  <h3 class="svc-title">Regular Property<br>Inspections</h3>
  <p class="svc-text">Routine inspections to maintain<br>property condition and address issues<br>before they become costly problems.</p>
</div>
<div class="abs svc" style="left:450px;top:1507px">
  <div class="svc-icon" role="img" aria-label="Legal document icon"></div>
  <h3 class="svc-title">Legal Compliance</h3>
  <p class="svc-text">Expertise in local and federal rental<br>laws to keep your properties<br>compliant and avoid legal hassles.</p>
</div>
<div class="abs svc" style="left:785px;top:1507px">
  <div class="svc-icon" role="img" aria-label="Financial report icon"></div>
  <h3 class="svc-title">Transparent Reporting</h3>
  <p class="svc-text">Detailed monthly reports and financial<br>statements to keep you informed<br>about your property's performance.</p>
</div>

<nav class="abs pager">
  <span class="word">PREVIOUS</span>
  <span class="num cur">01</span><span class="num">02</span><span class="num">03</span><span class="num">04</span><span class="num">05</span>
  <span class="word">NEXT</span>
</nav>

<footer class="abs footer">
  <div class="footer-inner"></div>
  <div class="abs foot-brand"><span class="brand-dot"></span>VELMORQUAY REALTY</div>
  <div class="abs foot-links">HOME<span>|</span>RESIDENTS<span>|</span>INVESTORS<span>|</span>COMMUNITIES<span>|</span>CONTACT US</div>
  <div class="abs copy">@2024 COPYRIGHTS<span>|</span>ALL RIGHTS RESERVED</div>
</footer>

</body>
</html>
```